WP website design (Harrowgate)

We need a wordpress design for an established auction and real estate company based in Florida. The winning design will incorporate a professional color scheme with company logo in a clean layout. The design needs to consider that this will be developed on a responsive theme. Colors are those that will highlight the logo.

Industry/Entity Type

Real Estate

Font styles to use
Serif
Sans Serif

Colors

Designer to choose colors to be used in the design.

Requirements
Must have
• Navigation:
1) Home
2) Auctions
3) Online Auctions
4) About Us
5) Services
6) Real Estate Listings
7) References
8) Contact Us

Colors will be blue (#000066) / red (#B10000) and black or other complementary color. Tagline to be used "Since 1977, Proven Results." Slideshow to be placed in the header or body of home page - please use stock real estate image.

Widgets: 1) Email Sign-up 2) Social media icons for FB and LinkedIn 3) Featured Listings 4) Testimonials 5) Register button

Footer will have smaller company logo, attached logos and contact info:
Phone: (555) 261-0948 Mobile: (555) 718-3062
Email: mirelharrowgate@quellmail.example
Address: 58 E. Tamsin Avenue, Ste 410, Calder Bay, FL 32599
Nice to have
• Use of a drop down menu:
Auctions-
1) Upcoming Auctions
2) Past Auctions

```html
<!DOCTYPE html>
<html lang="en">
<head>
<meta charset="utf-8">
<title>Harrowgate Auctions</title>
<link href="https://fonts.googleapis.com/css2?family=Open+Sans:wght@400;600;700&display=swap" rel="stylesheet">
<style>
:root{
  --navy:#000066;
  --red:#b10000;
  --ink:#222;
  --muted:#666;
  --line:#ddd;
  --panel:#f2f2f2;
  --bar:#e9e9e9;
  --white:#fff;
}
*{box-sizing:border-box;margin:0;padding:0}
html,body{width:800px;height:1200px;overflow:hidden}
body{
  font-family:"Open Sans",Arial,sans-serif;color:var(--ink);font-size:8px;line-height:1.5;
  background:linear-gradient(180deg,#f3d3d6 0%,#fbeff0 18%,#ffffff 45%,#eceef8 75%,#cfd3ec 100%);
}
.page{position:absolute;left:30px;top:0;width:740px;height:1200px;background:var(--white)}
.header{height:80px;position:relative}
.brand{position:absolute;left:24px;top:22px;display:flex;align-items:center;gap:8px}
.brand-mark{width:26px;height:26px;background:var(--red)}
.brand-name{font-size:24px;font-weight:700;color:var(--navy);line-height:1}
.register{position:absolute;right:22px;top:30px;background:var(--navy);color:#fff;font-size:8px;font-weight:600;padding:6px 16px;text-transform:uppercase}
.nav{height:22px;background:var(--bar);display:flex;padding-left:14px;position:relative}
.nav a{font-size:7.5px;font-weight:600;color:#444;text-decoration:none;padding:0 12px;line-height:22px;text-transform:uppercase}
.nav a.active{background:var(--red);color:#fff}
.dropdown{position:absolute;left:66px;top:22px;background:var(--navy);width:96px;z-index:2;padding:4px 0}
.dropdown span{display:block;color:#fff;font-size:7px;padding:4px 10px;text-transform:uppercase}
.hero{height:278px;position:relative;background:linear-gradient(180deg,#6a5fb4 0%,#9c7fc6 45%,#5e78b0 75%,#2e4a72 100%)}
.tagline{position:absolute;right:16px;bottom:22px;background:rgba(0,0,102,.8);color:#fff;font-size:14px;padding:6px 12px}
.section{padding:0 24px}
.sec-head{display:flex;justify-content:space-between;align-items:baseline;margin-top:24px;border-bottom:1px solid var(--line);padding-bottom:5px}
.sec-head h2{font-size:14px;font-weight:700;color:var(--navy)}
.view-all{color:var(--red);font-size:8px;font-weight:600}
.listings{display:flex;gap:24px;margin-top:10px}
.listing{flex:1}
.listing .photo{height:84px;background:linear-gradient(180deg,#9fc3e6 0%,#c9d8e4 50%,#7a8f5a 100%)}
.listing p{font-size:7px;color:var(--muted);margin-top:5px}
.cols{display:flex;gap:24px;margin-top:44px}
.col{flex:1}
.col h3,.block h3{font-size:11px;font-weight:700;color:var(--navy);border-bottom:1px solid var(--line);padding-bottom:4px;margin-bottom:7px}
.col p{color:var(--muted);font-size:7px}
.col ul{list-style:none;margin:10px 0 0 20px}
.col li{color:var(--red);font-size:7.5px;font-weight:600;padding:1.5px 0}
.col li::before{content:"";display:inline-block;width:4px;height:4px;background:var(--red);margin-right:6px;vertical-align:middle}
.duo{display:flex;gap:24px;margin-top:42px}
.block{flex:1}
.quote{color:var(--muted);font-size:7px;margin-bottom:10px}
.author{text-align:right;color:var(--red);font-size:7px}
.auction{display:flex;gap:10px}
.auction .thumb{width:80px;height:66px;background:linear-gradient(180deg,#a9c7e0,#8a9a6b)}
.auction h4{font-size:7.5px;color:var(--ink);font-weight:600}
.price-row{display:flex;align-items:center;gap:14px;margin:3px 0}
.price{font-size:16px;font-weight:700;color:var(--ink)}
.timer{color:var(--red);font-size:8px;font-weight:600}
.auction p{font-size:7px;color:var(--muted)}
.bid{display:inline-block;background:var(--navy);color:#fff;font-size:7px;font-weight:600;padding:3px 16px;margin-top:4px}
.partners{display:flex;justify-content:space-between;align-items:center;margin:28px 24px 0;padding:0 12px;height:56px;background:var(--panel)}
.badge{height:28px;background:#b8b8b8}
.footer-boxes{display:flex;gap:12px;margin:16px 24px 0}
.fbox{flex:1;background:var(--panel);height:172px;padding:0 10px 10px}
.fbox h3{font-size:10px;color:var(--navy);font-weight:700;border-bottom:1px solid #ccc;padding:10px 0 6px;margin-bottom:10px}
.small-brand{display:flex;align-items:center;gap:5px;margin-bottom:6px}
.small-brand .brand-mark{width:14px;height:14px}
.small-brand span{font-size:13px;font-weight:700;color:var(--navy)}
.fbox p{font-size:7px;color:var(--muted)}
.contact-row{display:flex;align-items:center;gap:6px;font-size:7px;color:#444;margin-bottom:7px}
.contact-row svg{flex:none}
.contact-row.email{color:var(--red)}
.field{height:20px;background:#fff;border:1px solid #ccc;margin-top:10px}
.submit{display:block;margin:8px 0 0 auto;width:56px;background:var(--navy);color:#fff;font-size:7px;font-weight:600;text-align:center;padding:5px 0}
.bottom{display:flex;justify-content:space-between;align-items:center;margin:12px 24px 0;border-top:1px solid var(--line);padding-top:8px;font-size:7px;color:var(--muted)}
.bottom .policy{color:var(--red);margin-left:8px}
.social{display:flex;gap:5px}
.social span{width:14px;height:14px;background:var(--navy);display:block}
</style>
</head>
<body>
<div class="page">
  <header class="header">
    <div class="brand"><span class="brand-mark"></span><span class="brand-name">Harrowgate</span></div>
    <span class="register">Register</span>
  </header>
  <nav class="nav">
    <a class="active">Home</a><a>Auctions</a><a>Online Auctions</a><a>About Us</a><a>Services</a><a>Real Estate Listings</a><a>References</a><a>Contact Us</a>
    <div class="dropdown"><span>Upcoming Auctions</span><span>Past Auctions</span></div>
  </nav>
  <div class="hero" role="img" aria-label="City skyline of high-rise towers at dusk">
    <div class="tagline">Since 1977, Proven Results</div>
  </div>

  <section class="section">
    <div class="sec-head"><h2>Featured Listings</h2><span class="view-all">View All</span></div>
    <div class="listings">
      <div class="listing"><div class="photo" role="img" aria-label="Photo of a two-storey family home"></div><p>Lorem ipsum dolor sit amet consectetur</p></div>
      <div class="listing"><div class="photo" role="img" aria-label="Photo of a suburban house with lawn"></div><p>Lorem ipsum dolor sit amet consectetur</p></div>
      <div class="listing"><div class="photo" role="img" aria-label="Photo of a large residential home"></div><p>Lorem ipsum dolor sit amet consectetur</p></div>
    </div>

    <div class="cols">
      <div class="col"><h3>Getting Started</h3><p>Duis aute irure dolor in reprehenderit in voluptate velit esse cillum dolore eu fugiat nulla pariatur excepteur sint.</p>
        <ul><li>Overview</li><li>Creating an Account</li><li>Register</li><li>Bid</li></ul></div>
      <div class="col"><h3>Buying</h3><p>Duis aute irure dolor in reprehenderit in voluptate velit esse cillum dolore eu fugiat nulla pariatur excepteur sint.</p>
        <ul><li>Residential</li><li>Foreclosure</li><li>Commercial</li><li>For Agents &amp; Brokers</li></ul></div>
      <div class="col"><h3>Selling</h3><p>Duis aute irure dolor in reprehenderit in voluptate velit esse cillum dolore eu fugiat nulla pariatur excepteur sint.</p>
        <ul><li>Commercial</li><li>For Agents &amp; Brokers</li></ul></div>
    </div>

    <div class="duo">
      <div class="block"><h3>Testimonials</h3>
        <p class="quote">"Travel sunlight various cubically unpleasantly frank. Nullam velit; thought, fertile honest dreadfully rising. Morbi nulla pure dolor. Sed quis ante vitae lorem tempor gravida, porta nunc."</p>
        <p class="quote">"Travel sunlight various cubically unpleasantly frank. Nullam velit; thought, fertile honest dreadfully rising. Morbi nulla pure dolor. Sed quis ante vitae lorem tempor gravida, porta nunc."</p>
        <p class="author">- john doe<br>Location</p>
      </div>
      <div class="block"><h3>Online Auctions</h3>
        <div class="auction">
          <div class="thumb" role="img" aria-label="Photo of the house up for auction"></div>
          <div>
            <h4>Travel sunlight various cubically</h4>
            <div class="price-row"><span class="price">$ 250.00</span><span class="timer">00 : 00 : 00</span></div>
            <p>Lorem ipsum dolor sit amet, consectetur adipiscing elit sed do eiusmod tempor.</p>
            <span class="bid">BID</span>
          </div>
        </div>
      </div>
    </div>
  </section>

  <div class="partners" aria-label="Partner associations">
    <span class="badge" style="width:60px"></span>
    <span class="badge" style="width:110px"></span>
    <span class="badge" style="width:80px"></span>
    <span class="badge" style="width:90px"></span>
    <span class="badge" style="width:100px"></span>
    <span class="badge" style="width:70px"></span>
  </div>

  <div class="footer-boxes">
    <div class="fbox"><h3>About Us</h3>
      <div class="small-brand"><span class="brand-mark"></span><span>Harrowgate</span></div>
      <p>Lorem ipsum dolor sit amet consectetur adipiscing elit sed do eiusmod tempor incididunt ut labore et dolore magna aliqua ut enim ad minim veniam quis nostrud exercitation ullamco laboris nisi ut aliquip ex ea commodo.</p>
    </div>
    <div class="fbox"><h3>Get in Touch</h3>
      <div class="contact-row"><svg width="10" height="10" viewBox="0 0 10 10"><path d="M2 1l2 2-1 1.2a6 6 0 0 0 2.8 2.8L7 6l2 2-1.5 1.5C4 9 1 6 .5 2.5z" fill="#000066"/></svg>(555) 261-0948</div>
      <div class="contact-row"><svg width="10" height="10" viewBox="0 0 10 10"><rect x="2.5" y="0.5" width="5" height="9" rx="1" fill="none" stroke="#000066"/><circle cx="5" cy="8" r=".6" fill="#000066"/></svg>(555) 718-3062</div>
      <div class="contact-row email"><svg width="10" height="10" viewBox="0 0 10 10"><rect x=".5" y="2" width="9" height="6" fill="none" stroke="#000066"/><path d="M.5 2l4.5 3.5L9.5 2" fill="none" stroke="#000066"/></svg>mirelharrowgate@quellmail.example</div>
      <div class="contact-row"><svg width="10" height="10" viewBox="0 0 10 10"><path d="M5 9.5S1.8 6 1.8 3.8a3.2 3.2 0 0 1 6.4 0C8.2 6 5 9.5 5 9.5z" fill="#000066"/><circle cx="5" cy="3.8" r="1.1" fill="#fff"/></svg>58 E. Tamsin Avenue, Ste 410,<br>Calder Bay, FL 32599</div>
    </div>
    <div class="fbox"><h3>Newsletter Signup</h3>
      <p>Enter your email address to receive our latest newsletters containing our latest auctions and listings.</p>
      <div class="field"></div>
      <span class="submit">SUBMIT</span>
    </div>
  </div>

  <div class="bottom">
    <div>Copyright 2013 &copy; Harrowgate. All Rights Reserved.<span class="policy">Privacy Policy</span></div>
    <div class="social"><span aria-label="Social profile"></span><span aria-label="Professional profile"></span></div>
  </div>
</div>
</body>
</html>
```